Harvest Lantern Jamboree Announcement on a 6x9 Postcard

I would like a 6x9 postcard mailer inviting people to our Harvest Lantern Jamboree at Cedarlight Church in Milwaukee Wisconsin. The template is included

Some activities would include:
School Supply Giveaway
Free Food
Bounce Houses
Face Painting
and more....

Date/Time: Saturday August 17th from 2pm to 4pm

Side 2 would have our Logo (We do have the AI or EPS file if needed), Date, Name, Address, QR Code, phone, Website Information.
Saturday, August 17 from 2pm-4pm
Cedarlight Church
4815 W. 37th Street
Milwaukee, WI 53288
Ph: 414-555-0172
Website: www.cedarlightfc.example
tagline: A Home Where Welcomed Friends Welcome Friends

Target Market(s)

Neighborhoods immediately surrounding our church who have young children in need of school supplies.

Industry/Entity Type

Christian Church

Colors
0054AA
0677BA
7BADD7
CADEEF
E8F1F8
EB3D1F
EC4F4E
F09395
F8D3D4
FCEDEE

Requirements
Nice to have
• I would like to have a picture of our building with additional pictures on the back side with some of the activities we will have.

```html
<!DOCTYPE html>
<html lang="en">
<head>
<meta charset="utf-8">
<title>Harvest Lantern Jamboree Postcard</title>
<link href="https://fonts.googleapis.com/css2?family=Poppins:wght@400;500;600;700&family=Oswald:wght@600;700&family=Yellowtail&display=swap" rel="stylesheet">
<style>
  :root{
    --backdrop:#656565;
    --red:#bf210e;
    --purple:#2f1b6c;
    --purple-soft:#4a3590;
    --ink:#2b2b2b;
    --white:#ffffff;
    --postage:#e1e1e1;
  }
  *{box-sizing:border-box;margin:0;padding:0}
  html,body{width:847px;height:1200px;overflow:hidden;background:var(--backdrop)}
  body{position:relative;font-family:'Poppins',sans-serif}
  .card{position:absolute;left:75px;width:710px;background:var(--white);overflow:hidden}
  .front{top:99px;height:474px}
  .back{top:614px;height:479px}
  .abs{position:absolute}
  .shapes{position:absolute;left:0;top:0}
  .brand{position:absolute;display:flex;align-items:center;gap:8px;color:var(--purple);font-weight:600;white-space:nowrap}
  .brand-dot{width:14px;height:14px;border-radius:50%;background:var(--red);flex:none}

  /* front */
  .front .brand{left:0;width:355px;justify-content:center;top:44px;font-size:26px}
  .title{position:absolute;left:15px;width:290px;text-align:center;white-space:nowrap}
  .title-small{top:118px;font-size:34px;font-weight:500;color:var(--ink);letter-spacing:1px}
  .title-big{top:148px;font-family:'Oswald',sans-serif;font-weight:700;font-size:84px;line-height:1;color:var(--red);letter-spacing:-1px}
  .title-script{top:226px;font-family:'Yellowtail',cursive;font-size:54px;color:var(--purple);line-height:1}
  .day-num{position:absolute;font-weight:700;line-height:1;letter-spacing:-3px}
  .front .day-num{left:308px;top:254px;font-size:54px;color:var(--red)}
  .front .month{left:366px;top:262px;color:var(--white);font-weight:700;font-size:19px;line-height:24px}
  .front .weekday{left:503px;top:250px;color:var(--white);font-weight:700;font-size:22px;letter-spacing:.5px}
  .time{position:absolute;display:flex;align-items:center;gap:10px;font-weight:600;font-size:24px;color:var(--white)}
  .time-to{width:26px;height:26px;border-radius:50%;display:flex;align-items:center;justify-content:center;font-size:12px;font-weight:600}
  .front .time{left:503px;top:275px}
  .front .time-to{background:var(--red)}
  .activity{position:absolute;top:327px;height:71px;display:flex}
  .activity-photo{width:85px;height:71px}
  .activity-label{height:71px;display:flex;align-items:center;padding-left:9px;color:var(--white);font-size:10.5px;font-weight:500;line-height:13px;white-space:nowrap}
  .red{background:var(--red)}
  .purple{background:var(--purple)}
  .contact-band{position:absolute;left:0;top:398px;width:325px;height:76px;background:var(--red)}
  .contact-phone{position:absolute;left:38px;top:410px;display:flex;align-items:center;gap:14px;color:var(--white);font-weight:600;font-size:29px}
  .contact-web{position:absolute;left:335px;top:416px;display:flex;align-items:center;gap:14px;color:var(--ink);font-weight:500;font-size:22px}

  /* back */
  .tagline-script{left:72px;top:30px;font-family:'Yellowtail',cursive;font-size:50px;color:var(--white);line-height:1;white-space:nowrap}
  .tagline-line{left:70px;font-size:38px;font-weight:400;color:var(--white);line-height:1;letter-spacing:.5px;white-space:nowrap}
  .back .brand{left:478px;width:232px;justify-content:center;top:82px;font-size:20px}
  .back .day-num{left:44px;top:236px;font-size:68px;color:var(--white)}
  .back .month{left:115px;top:245px;color:var(--white);font-weight:700;font-size:23px;line-height:25px}
  .weekday-box{left:42px;top:308px;width:186px;height:25px;background:var(--white);color:var(--purple);font-weight:700;font-size:21px;line-height:25px;text-align:center}
  .back .time{left:50px;top:333px}
  .back .time-to{background:var(--purple)}
  .church-name{left:34px;top:384px;font-weight:700;font-size:17px;color:var(--purple);white-space:nowrap}
  .back-phone{left:29px;top:411px;display:flex;align-items:center;gap:6px;font-weight:600;font-size:20px;color:var(--ink);white-space:nowrap}
  .back-web{left:29px;top:443px;display:flex;align-items:center;gap:6px;font-weight:500;font-size:11px;color:var(--ink);white-space:nowrap}
  .address{left:222px;top:430px;display:flex;gap:6px;font-weight:500;font-size:12px;line-height:16px;color:var(--ink);white-space:nowrap}
</style>
</head>
<body>

<section class="card front">
  <svg class="shapes" width="710" height="474" viewBox="0 0 710 474">
    <defs>
      <linearGradient id="churchPhoto" x1="0" y1="0" x2="0" y2="1">
        <stop offset="0" stop-color="#d7d9d8"/>
        <stop offset=".45" stop-color="#8c5a45"/>
        <stop offset=".8" stop-color="#5f7f3c"/>
        <stop offset="1" stop-color="#4c6d30"/>
      </linearGradient>
    </defs>
    <rect x="359" y="0" width="351" height="242" fill="url(#churchPhoto)" role="img" aria-label="Photo of the church building"/>
    <polygon points="337.7,311.7 354.6,248.5 430.9,248.5 450.6,206.1 476,311.7" fill="var(--purple)"/>
    <polygon points="481.7,311.7 495.8,244.5 710,244.5 710,311.7" fill="var(--purple)"/>
    <polyline points="357,0 357,244 430,244 451,194 477,305 492,239 710,239" fill="none" stroke="var(--red)" stroke-width="4"/>
  </svg>

  <div class="brand"><span class="brand-dot"></span>Cedarlight Church</div>

  <div class="title title-small">HARVEST</div>
  <div class="title title-big">LANTERN</div>
  <div class="title title-script">Jamboree</div>

  <div class="day-num">17</div>
  <div class="abs month">AUGUST<br>2024</div>
  <div class="abs weekday">SATURDAY</div>
  <div class="time">2PM <span class="time-to red">TO</span> 4PM</div>

  <div class="contact-band"></div>

  <div class="activity" style="left:38px">
    <div class="activity-photo" style="background:linear-gradient(135deg,#b98f6a,#4aa0d8)" role="img" aria-label="Photo of a school backpack with supplies"></div>
    <div class="activity-label red" style="width:71px">School<br>Supply<br>Giveaway</div>
  </div>
  <div class="activity" style="left:202px">
    <div class="activity-photo" style="background:linear-gradient(135deg,#4f7a3a,#e0463a 55%,#3aa3d6)" role="img" aria-label="Photo of an inflatable bounce house"></div>
    <div class="activity-label purple" style="width:66px">Bounce<br>Houses</div>
  </div>
  <div class="activity" style="left:360px">
    <div class="activity-photo" style="background:linear-gradient(135deg,#5d7a3a,#8a5a3a 50%,#c59a3a)" role="img" aria-label="Photo of food on a grill"></div>
    <div class="activity-label red" style="width:66px">Free<br>Food</div>
  </div>
  <div class="activity" style="left:518px">
    <div class="activity-photo" style="background:linear-gradient(135deg,#6b4a36,#d8d2cc)" role="img" aria-label="Photo of face painting at the event"></div>
    <div class="activity-label purple" style="width:68px">Face<br>Painting<br>and more..</div>
  </div>

  <div class="contact-phone">
    <svg width="18" height="18" viewBox="0 0 24 24" aria-hidden="true"><path d="M6.6 10.8a15 15 0 0 0 6.6 6.6l2.2-2.2c.3-.3.7-.4 1-.2 1.1.4 2.3.6 3.6.6.6 0 1 .4 1 1V20c0 .6-.4 1-1 1A17 17 0 0 1 3 4c0-.6.4-1 1-1h3.5c.6 0 1 .4 1 1 0 1.3.2 2.5.6 3.6.1.3 0 .7-.2 1z" fill="none" stroke="#fff" stroke-width="2"/></svg>
    414-555-0172
  </div>
  <div class="contact-web">
    <svg width="22" height="22" viewBox="0 0 24 24" aria-hidden="true"><circle cx="12" cy="12" r="10" fill="none" stroke="var(--purple)" stroke-width="2"/><path d="M2 12h20M12 2c3 3 3 17 0 20M12 2c-3 3-3 17 0 20" fill="none" stroke="var(--purple)" stroke-width="1.6"/></svg>
    www.cedarlightfc.example
  </div>
</section>

<section class="card back">
  <svg class="shapes" width="710" height="479" viewBox="0 0 710 479">
    <defs>
      <linearGradient id="crowdPhoto" x1="0" y1="0" x2="0" y2="1">
        <stop offset="0" stop-color="#c9c2c4"/>
        <stop offset=".4" stop-color="#7d6a62"/>
        <stop offset="1" stop-color="#3b3340"/>
      </linearGradient>
    </defs>
    <rect x="3" y="0" width="473" height="221" fill="var(--purple-soft)" role="img" aria-label="Purple-tinted photo of the church building"/>
    <rect x="3" y="0" width="473" height="221" fill="var(--purple)" opacity=".55"/>
    <rect x="566" y="249" width="144" height="230" fill="var(--postage)"/>
    <rect x="377" y="418" width="190" height="61" fill="var(--postage)"/>
    <polygon points="270,221 566,221 566,418 252,418 252,267" fill="url(#crowdPhoto)" role="img" aria-label="Photo of a crowd seated outdoors at an evening gathering"/>
    <polygon points="0,220 202,220 230,173 252,267 252,372 0,372" fill="var(--red)"/>
    <polyline points="252,267 270,221 478,221 478,0" fill="none" stroke="var(--red)" stroke-width="3"/>
  </svg>

  <div class="abs tagline-script">A Home Where</div>
  <div class="abs tagline-line" style="top:88px">WELCOMED FRIENDS</div>
  <div class="abs tagline-line" style="top:140px">WELCOME FRIENDS</div>

  <div class="brand"><span class="brand-dot"></span>Cedarlight Church</div>

  <div class="day-num">17</div>
  <div class="abs month">AUGUST<br>2024</div>
  <div class="abs weekday-box">SATURDAY</div>
  <div class="time">2PM <span class="time-to purple">TO</span> 4PM</div>

  <div class="abs church-name">CEDARLIGHT CHURCH</div>
  <div class="abs back-phone">
    <svg width="14" height="14" viewBox="0 0 24 24" aria-hidden="true"><path d="M6.6 10.8a15 15 0 0 0 6.6 6.6l2.2-2.2c.3-.3.7-.4 1-.2 1.1.4 2.3.6 3.6.6.6 0 1 .4 1 1V20c0 .6-.4 1-1 1A17 17 0 0 1 3 4c0-.6.4-1 1-1h3.5c.6 0 1 .4 1 1 0 1.3.2 2.5.6 3.6.1.3 0 .7-.2 1z" fill="none" stroke="var(--purple)" stroke-width="2.4"/></svg>
    414-555-0172
  </div>
  <div class="abs back-web">
    <svg width="13" height="13" viewBox="0 0 24 24" aria-hidden="true"><circle cx="12" cy="12" r="10" fill="none" stroke="var(--purple)" stroke-width="2.4"/><path d="M2 12h20M12 2c3 3 3 17 0 20M12 2c-3 3-3 17 0 20" fill="none" stroke="var(--purple)" stroke-width="2"/></svg>
    www.cedarlightfc.example
  </div>
  <div class="abs address">
    <svg width="14" height="16" viewBox="0 0 24 28" aria-hidden="true"><path d="M12 2a8 8 0 0 0-8 8c0 6 8 14 8 14s8-8 8-14a8 8 0 0 0-8-8z" fill="none" stroke="var(--purple)" stroke-width="2.4"/><circle cx="12" cy="10" r="3" fill="none" stroke="var(--purple)" stroke-width="2.4"/><path d="M5 26h14" stroke="var(--purple)" stroke-width="2.4"/></svg>
    <div>4815 W. 37th Street<br>Milwaukee, WI 53288</div>
  </div>
</section>

</body>
</html>
```